Foot and ankle surgeon requires a website design

I need a website where prospective and established patients can obtain information and then direct them to making appointments. My practice is a highly professional surgical practice specialising in surgery to the foot and ankle. My title is Mr Colin Brasket, Podiatric Foot & Ankle Surgeon. My qualifications are: BSc MSc FACPS
The practice website will require information on: Locations, phone numbers to make appointments, general background on podiatric surgery,
I would like to include information on: my hospital appointments, surgical fellowships held, training programs undertaken, association memberships, publications written, links to useful websites
A page dedicated to common foot conditions would be useful and also a page with referral information including an online registration section that will be sent direct to the receptionist.
Examples of similar websites include:
http://www.dorvelquintaro.com.au/
http://www.haldenfootsurgeon.com.au/
I will provide files on logo, self photos and my personal training history etc.
Also if there is going to be a background theme I personally am associated with surfing and beach activities, it would be great if this was able to be reflected in the design.
Thank you.

```html
<!DOCTYPE html>
<html lang="en">
<head>
<meta charset="utf-8">
<title>Mr Colin Brasket – Podiatric Foot &amp; Ankle Surgeon</title>
<link href="https://fonts.googleapis.com/css2?family=Arimo:ital,wght@0,400;0,700;1,400;1,700&family=Open+Sans:wght@400;700&family=Tinos:wght@400;700&display=swap" rel="stylesheet">
<style>
:root{
  --blue:#1d5594;
  --blue-dark:#0f3c72;
  --navy:#163f6e;
  --orange:#f47a20;
  --white:#ffffff;
  --grey-bg:#f4f4f4;
  --text:#333333;
  --border:#d8d8d8;
  --footer:#3b3b3b;
}
*{margin:0;padding:0;box-sizing:border-box}
html,body{width:847px;height:1200px;overflow:hidden}
body{position:relative;font-family:"Arimo",Arial,sans-serif;color:var(--text);background:var(--white)}
.abs{position:absolute}

/* header band */
.header-band{left:0;top:0;width:847px;height:463px;background:linear-gradient(180deg,#2f69a8 0%,#1f5898 45%,#164a85 100%)}
.brand{left:74px;top:20px;display:flex;align-items:center;gap:10px}
.brand-mark{width:28px;height:28px;border-radius:50%;background:var(--orange)}
.brand-name{font-family:"Tinos",serif;font-weight:700;font-size:18px;color:var(--white);line-height:1}
.brand-tag{font-family:"Tinos",serif;font-size:9px;color:var(--orange);margin-top:3px}
.call{right:71px;top:46px;display:flex;align-items:center;gap:8px;color:var(--white);font-size:15px}
.nav{left:229px;top:106px;display:flex;font-size:12px;color:var(--white)}
.nav span{height:27px;line-height:27px;padding:0 12.5px}
.nav .active{background:var(--orange);padding:0 12px;width:57px}

.hero{left:72px;top:142px;width:706px;height:282px;border:3px solid var(--white);box-shadow:0 12px 18px rgba(0,0,0,.35)}
.hero-photo{width:100%;height:100%;background:linear-gradient(180deg,#5a8fc0 0%,#9cc0de 35%,#d9b5a8 60%,#ebe6e2 100%)}
.hero-panel{left:3px;top:76px;width:315px;height:150px;background:rgba(40,35,35,.82);padding:8px 18px}
.hero-title{font-family:"Open Sans",sans-serif;font-weight:700;font-size:24px;color:var(--white);letter-spacing:1px}
.hero-sub{font-family:"Open Sans",sans-serif;font-size:16px;color:var(--orange);margin-top:-1px}
.hero-copy{font-size:10px;line-height:17px;color:var(--white);margin-top:2px}
.btn{background:var(--orange);color:var(--white);border-radius:3px;text-align:center}
.hero-btn{width:85px;height:24px;line-height:24px;font-size:10px;margin-top:8px}

/* feature cards */
.card{top:514px;width:213px;height:106px;border:1px solid var(--border);border-bottom:3px solid var(--navy);background:var(--white);text-align:center;padding-top:30px}
.card-icon{top:481px;width:58px;height:58px;border-radius:50%;border:2px solid var(--navy);background:var(--white);display:flex;align-items:center;justify-content:center}
.card-kicker{font-size:12px;color:var(--blue)}
.card-title{font-weight:700;font-size:13px;color:var(--navy);letter-spacing:.5px}
.card-text{font-size:8.5px;line-height:13px;margin-top:6px;color:#222}

/* grey content area */
.content-bg{left:0;top:640px;width:847px;height:468px;background:var(--grey-bg)}
.section-title{font-family:"Tinos",serif;font-size:21px;color:#444}
.section-title b{font-weight:400;color:var(--blue)}
.doctor-photo{left:78px;top:689px;width:152px;height:145px;border:5px solid var(--white);box-shadow:0 0 3px rgba(0,0,0,.2);background:linear-gradient(180deg,#f2f2f2 0%,#dcdcdc 100%)}
.about-copy{left:246px;top:689px;width:532px;font-size:9.6px;line-height:15.6px;color:#444}
.about-copy p+p{margin-top:15.6px}
.divider{left:73px;top:850px;width:703px;border-top:1px dashed #cfcfcf}

.booking{left:75px;top:864px;width:235px;height:233px;border:1px dashed #cfcfcf;background:var(--grey-bg)}
.booking-head{height:28px;background:var(--blue);color:var(--white);font-family:"Tinos",serif;font-size:19px;padding:3px 8px}
.field{left:10px;width:214px;height:23px;border:1px solid #d0d0d0;border-radius:3px;background:linear-gradient(#fafafa,#ececec);font-style:italic;font-size:8.5px;color:#666;padding:6px 8px}
.book-btn{left:33px;top:198px;width:155px;height:24px;line-height:24px;font-weight:700;font-size:12px}

.tab{top:901px;height:27px;color:var(--white);font-family:"Tinos",serif;font-size:14px;text-align:center;line-height:27px}
.news-box{left:355px;top:928px;width:415px;height:168px;border:1px solid var(--border);background:var(--white)}
.news-photo{left:7px;top:12px;width:95px;height:67px;background:linear-gradient(135deg,#4f9a9c,#8fc7c8 55%,#3b7270)}
.news-copy{font-size:8.4px;line-height:14px;color:#333;text-align:justify}
.read-more{right:10px;bottom:8px;font-size:8px;font-weight:700;font-style:italic;color:var(--blue)}

/* footer */
.footer{left:0;top:1108px;width:847px;height:92px;background:var(--footer)}
.foot-brand{left:78px;top:1140px;display:flex;align-items:center;gap:8px}
.foot-links{right:71px;top:1133px;font-size:9.6px;color:var(--white);word-spacing:2px}
.social{left:333px;top:1160px;display:flex;align-items:center;gap:9px;font-size:8.5px;font-style:italic;color:#aaa}
.social i{display:block;width:19px;height:19px;border-radius:3px;background:#d8d8d8}
.copyright{right:71px;top:1164px;font-size:9.6px;color:var(--white)}
</style>
</head>
<body>

<div class="abs header-band"></div>

<div class="abs brand">
  <div class="brand-mark"></div>
  <div>
    <div class="brand-name">Mr Colin Brasket</div>
    <div class="brand-tag">Podiatric Foot &amp; Ankle Surgeon</div>
  </div>
</div>

<div class="abs call">
  <svg width="32" height="32" viewBox="0 0 32 32"><circle cx="16" cy="16" r="14.5" fill="none" stroke="#fff" stroke-width="2"/><path d="M12 8c-2 1-3 3-2 6 1 4 4 8 8 10 2 1 4 0 5-2l-3-3-2 1c-2-1-4-4-5-6l1-2z" fill="#fff"/></svg>
  <span>Call Us : 08 9400 1275</span>
</div>

<nav class="abs nav">
  <span class="active">Home</span><span>About Us</span><span>Foot Conditions</span><span>Treatments</span><span>Surgery</span><span>Employment</span><span>Our Locations</span>
</nav>

<div class="abs hero">
  <div class="hero-photo" role="img" aria-label="Sandy bare feet on the beach against a blue sky"></div>
  <div class="abs hero-panel">
    <div class="hero-title">MR.COLIN BRASKET</div>
    <div class="hero-sub">Podiatric Foot &amp; Ankle Surgeon</div>
    <div class="hero-copy">Lorem ipsum dolor sit amet, consectetuer adipiscing elit, sed diam nonummy nibh euismod tincidunt ut laoreet dolore magna aliquam erat volutpat.</div>
    <div class="btn hero-btn">READ MORE</div>
  </div>
</div>

<!-- feature cards -->
<div class="abs card" style="left:73px">
  <div class="card-kicker">MY HOPITAL</div>
  <div class="card-title">APPOINTMENT</div>
  <div class="card-text">Lorem ipsum dolor sit amet, consectetur<br>adipisicing elit, sed eiusmodtempor</div>
</div>
<div class="abs card-icon" style="left:150px">
  <svg width="34" height="30" viewBox="0 0 34 30"><rect x="2" y="5" width="26" height="21" rx="2" fill="none" stroke="#163f6e" stroke-width="2"/><rect x="2" y="5" width="26" height="5" fill="#163f6e"/><g fill="#163f6e"><rect x="6" y="13" width="3" height="3"/><rect x="11" y="13" width="3" height="3"/><rect x="16" y="13" width="3" height="3"/><rect x="6" y="18" width="3" height="3"/><rect x="11" y="18" width="3" height="3"/></g><circle cx="26" cy="23" r="6" fill="#fff" stroke="#163f6e" stroke-width="2"/><path d="M26 20v3h3" stroke="#163f6e" stroke-width="1.5" fill="none"/></svg>
</div>

<div class="abs card" style="left:318px">
  <div class="card-kicker">SURGICAL</div>
  <div class="card-title">FELLOWSHIPS HELD</div>
  <div class="card-text">Lorem ipsum dolor sit amet, consectetur<br>adipisicing elit, sed eiusmodtempor</div>
</div>
<div class="abs card-icon" style="left:395px">
  <svg width="36" height="22" viewBox="0 0 36 22"><rect x="1" y="2" width="3" height="19" fill="#163f6e"/><rect x="32" y="10" width="3" height="11" fill="#163f6e"/><rect x="1" y="14" width="34" height="3" fill="#163f6e"/><circle cx="9" cy="10" r="3" fill="#163f6e"/><rect x="13" y="8" width="19" height="5" rx="2" fill="#163f6e"/></svg>
</div>

<div class="abs card" style="left:562px">
  <div class="card-kicker">TRAINING</div>
  <div class="card-title">PROGRAMS</div>
  <div class="card-text">Lorem ipsum dolor sit amet, consectetur<br>adipisicing elit, sed eiusmodtempor</div>
</div>
<div class="abs card-icon" style="left:639px">
  <svg width="32" height="30" viewBox="0 0 32 30"><rect x="9" y="3" width="20" height="15" fill="none" stroke="#163f6e" stroke-width="2"/><rect x="4" y="12" width="5" height="16" fill="#163f6e"/></svg>
</div>

<!-- grey content -->
<div class="abs content-bg"></div>
<h2 class="abs section-title" style="left:82px;top:649px">About <b>Doctor</b></h2>
<div class="abs doctor-photo" role="img" aria-label="Portrait of the surgeon in a white coat with stethoscope"></div>
<div class="abs about-copy">
  <p>Lorem ipsum dolor sit amet, consectetur adipisicing elit, sed do eiusmod tempor incididunt ut labore et dolore magna &nbsp;Ut enim ad minim veniam, quis nostrud exercitation ullamco laboris nisi ut aliquip ex commodo consequat. Duis aute irure dolor in reprehenderit in voluptate velit esse cillum dolore eu fugiat nulla pariatur. Excepteur sint occaecat cupidatat non proident, sunt in culpa qui &nbsp;mollit anim id est laborum.</p>
  <p>&nbsp;inventore veritatis et quasi architecto beatae vitae dicta sunt explicabo. Nemo enim ipsam voluptatem quia voluptas &nbsp;sed quia consequuntur magni dolores eos qui ratione voluptatem sequi nesciunt. Neque porro quisquam est, qui dolorem dolore magnam aliquam quaerat voluptatem. Ut enim ad</p>
</div>
<div class="abs divider"></div>

<form class="abs booking">
  <div class="booking-head">Book an Appointment:</div>
  <div class="abs field" style="top:37px">Your Name</div>
  <div class="abs field" style="top:69px">Your Email</div>
  <div class="abs field" style="top:101px">Your Phone</div>
  <div class="abs field" style="top:130px;height:60px">Reason for Appointment</div>
  <div class="abs btn book-btn">Book Appointment</div>
</form>

<h2 class="abs section-title" style="left:355px;top:865px;color:var(--blue)">Health News</h2>
<div class="abs tab" style="left:355px;width:95px;background:#f58a3c">Recent</div>
<div class="abs tab" style="left:456px;width:96px;background:var(--blue)">Popular</div>
<div class="abs news-box">
  <div class="abs news-photo" role="img" aria-label="Surgeons in scrubs and masks operating"></div>
  <div class="abs news-copy" style="left:109px;top:10px;width:300px">Lorem ipsum dolor sit amet, consectetur adipisicing elit, sed do eiusmod tempor incididunt ut labore et dolore magna &nbsp;Ut enim ad minim veniam, quis nostrud exercitation ullamco laboris nisi ut aliquip ex commodo consequat. Duis aute irure dolor in reprehenderit in voluptate velit esse cillum dolore eu fugiat nulla pariatur. Excepteur sint occaecat cupidatat</div>
  <div class="abs news-copy" style="left:8px;top:90px;width:401px">Tempor incididunt ut labore et dolore magna &nbsp;Ut enim ad minim veniam, quis nostrud exercitation ullamco laboris nisi ut aliquip ex commodo consequat. Duis aute irure dolor in. Reprehenderit in voluptate velit esse cillum dolore eu fugiat nulla pariatur. Excepteur sint occaecat cupidatat Lorem ipsum dolor sit amet, consectetur adipisicing elit...</div>
  <div class="abs read-more">Read more...</div>
</div>

<!-- footer -->
<footer class="abs footer"></footer>
<div class="abs foot-brand">
  <div class="brand-mark" style="width:24px;height:24px"></div>
  <div>
    <div class="brand-name" style="font-size:15px">Mr Colin Brasket</div>
    <div class="brand-tag" style="font-size:8px">Podiatric Foot &amp; Ankle Surgeon</div>
  </div>
</div>
<div class="abs foot-links">Home &nbsp;| &nbsp;About Us &nbsp;| &nbsp;Foot Conditions &nbsp;| &nbsp;Treatments &nbsp;| &nbsp;Surgery &nbsp;| &nbsp;Employment &nbsp;| &nbsp;Our Locations</div>
<div class="abs social"><span>Get Connected</span><i></i><i></i><i></i></div>
<div class="abs copyright">Copyright © 2014 Mr Colin Brasket. All rights reserved.</div>

</body>
</html>
```